we can communicate on this, but i want to follow the approach we took on Pellew|Marsh & Quinlan but i feel the card front needs the black background and the platinum and gold logo. The back? I am open. we can use the same info from PM&Q. Velmont Arc is an enhanced equity investment fund - basically a very exclusive boutique hedge fund that uses only stock options. very advanced things. hope you are interested

Contact Information for Business Card

Dr. Lewis T. Brennick, CFA
Scientifique de fusée financière
701.555.0143
LTBquant47@mailvantor.com

4718 Willow Creek Bend W.
West Fargo, ND 58078

No web site

Colors

Designer to choose colors to be used in the design.

Requirements
Nice to have
• I tend to prefer the most visible applications of the logo to include logo and name, the logo version with a black background and the gold and platinum components separated by the black. I see this working well for a single side (logo and name - this is card front to me).
• I am fairly open to other treatments on the reverse side with the data. To me, it makes sense to have a different color rendition of the logo on the reverse and it may be a muted black tone on tone or an oversized portion that would have spot UV. Or, the reverse may play with colors and layout
Should not have
• Other colors = no no
• Decorative font

```html
<!DOCTYPE html>
<html lang="en">
<head>
<meta charset="utf-8">
<title>Velmont Arc — Business Card</title>
<link rel="stylesheet" href="https://fonts.googleapis.com/css2?family=Montserrat:ital,wght@0,300;0,400;0,500;0,600;1,400&display=swap">
<style>
  :root {
    --backdrop: #3b3b3d;
    --card-black: #151516;
    --gold: #d9ad2b;
    --gold-deep: #b98d16;
    --platinum: #f2f2f2;
    --silver: #b9b9bb;
  }
  * { margin: 0; padding: 0; box-sizing: border-box; }
  html, body {
    width: 800px; height: 1200px; overflow: hidden;
    background: var(--backdrop);
    font-family: "Montserrat", sans-serif;
  }
  .canvas { position: relative; width: 800px; height: 1200px; }
  .card {
    position: absolute; left: 80px;
    width: 640px; height: 366px;
    background: var(--card-black);
    border-radius: 4px;
    overflow: hidden;
    box-shadow: 0 10px 28px rgba(0,0,0,0.45);
  }
  .card--front { top: 150px; }
  .card--back  { top: 684px; }

  /* Front */
  .brand-mark {
    position: absolute; left: 50%; top: 56px;
    width: 118px; height: 118px; margin-left: -59px;
    border-radius: 50%;
    background: linear-gradient(135deg, var(--gold) 0%, var(--gold-deep) 100%);
  }
  .brand-name {
    position: absolute; left: 0; right: 0; top: 196px;
    text-align: center;
    color: var(--platinum);
    font-weight: 600; font-size: 46px; letter-spacing: 4px;
    text-transform: uppercase; line-height: 1;
  }
  .brand-name__sub {
    display: block; margin-top: 10px;
    color: var(--silver);
    font-weight: 300; font-size: 20px; letter-spacing: 10px;
  }

  /* Back */
  .back-accent {
    position: absolute; left: -190px; top: -100px;
    width: 460px; height: 460px; border-radius: 50%;
    background: linear-gradient(135deg, var(--gold) 0%, var(--gold-deep) 100%);
  }
  .details {
    position: absolute; right: 36px; top: 56px;
    text-align: right;
  }
  .details__brand {
    color: var(--gold);
    font-weight: 600; font-size: 32px; letter-spacing: 3px;
    text-transform: uppercase; line-height: 1;
  }
  .details__brand-sub {
    display: block; margin-top: 6px;
    color: var(--silver);
    font-weight: 300; font-size: 14px; letter-spacing: 8px;
  }
  .details__name {
    margin-top: 26px;
    color: var(--gold); font-weight: 500; font-size: 18px;
  }
  .details__role {
    margin-top: 2px;
    color: var(--platinum); font-style: italic; font-size: 13px;
  }
  .contact-list {
    list-style: none; margin-top: 16px;
    color: var(--silver); font-size: 13.5px; line-height: 1.55;
  }
  .contact-list li {
    display: flex; justify-content: flex-end; align-items: flex-start; gap: 10px;
  }
  .contact-list .icon {
    flex: none; width: 13px; height: 13px; margin-top: 4px;
  }
  .contact-list .icon * { fill: var(--gold); }
</style>
</head>
<body>
<main class="canvas">

  <section class="card card--front" aria-label="Card front">
    <div class="brand-mark"></div>
    <h1 class="brand-name">Velmont<span class="brand-name__sub">Arc</span></h1>
  </section>

  <section class="card card--back" aria-label="Card back">
    <div class="back-accent"></div>
    <div class="details">
      <div class="details__brand">Velmont<span class="details__brand-sub">Arc</span></div>
      <div class="details__name">Dr. Lewis T. Brennick, CFA</div>
      <div class="details__role">Scientifique de fusée financière</div>
      <ul class="contact-list">
        <li><span>701.555.0143</span>
          <svg class="icon" viewBox="0 0 16 16" aria-hidden="true"><rect x="0" y="0" width="16" height="16" rx="2"/></svg></li>
        <li><span>LTBquant47@mailvantor.com</span>
          <svg class="icon" viewBox="0 0 16 16" aria-hidden="true"><rect x="0" y="0" width="16" height="16" rx="2"/></svg></li>
        <li><span>4718 Willow Creek Bend W.,<br>West Fargo, ND 58078</span>
          <svg class="icon" viewBox="0 0 16 16" aria-hidden="true"><rect x="0" y="0" width="16" height="16" rx="2"/></svg></li>
      </ul>
    </div>
  </section>

</main>
</body>
</html>
```